Veldmark Supplies Business Card

Professional business card that stand out to our potential customers. Front and back with clean modern design

Industry/Entity Type

Oil and gas

Contact Information for Business Card

Name, address, website , office phone and cell number

Requirements
Must have
• Editable files for each employee

```html
<!DOCTYPE html>
<html lang="en">
<head>
<meta charset="utf-8">
<title>Veldmark Supplies Business Card</title>
<link href="https://fonts.googleapis.com/css2?family=Lato:wght@400;700&display=swap" rel="stylesheet">
<style>
  :root {
    --stage: #2b2b2b;
    --card: #1c1c1d;
    --card-back: #1a1a1b;
    --emboss: #0b0b0c;
    --red: #ff1a12;
    --cyan: #12b4d6;
    --white: #f2f2f2;
    --rule: #cfcfcf;
  }
  * { margin: 0; padding: 0; box-sizing: border-box; }
  html, body { width: 1200px; height: 694px; overflow: hidden; }
  body {
    background: var(--stage);
    font-family: "Lato", Arial, sans-serif;
    position: relative;
  }
  .card {
    position: absolute;
    top: 192px;
    width: 540px;
    height: 309px;
    border-radius: 18px;
    overflow: hidden;
  }
  .card-back { left: 30px; background: var(--card-back); }
  .card-front { left: 630px; background: var(--card); }

  /* back */
  .back-brand {
    position: absolute; inset: 0;
    display: flex; align-items: center; justify-content: center; gap: 14px;
  }
  .back-brand .mark { width: 34px; height: 34px; background: var(--emboss); }
  .back-brand .name {
    font-weight: 700; font-size: 36px; letter-spacing: 1px;
    color: var(--emboss); text-transform: uppercase;
  }

  /* front */
  .brand {
    position: absolute; top: 44px; right: 36px;
    display: flex; align-items: center; gap: 10px;
  }
  .brand .mark { width: 22px; height: 22px; background: var(--red); }
  .brand .name {
    font-weight: 700; font-size: 22px; letter-spacing: .5px;
    color: var(--white); text-transform: uppercase;
  }
  .person { position: absolute; left: 34px; top: 112px; }
  .person .full-name { color: var(--red); font-size: 28px; font-weight: 400; line-height: 1.1; }
  .person .role { color: var(--white); font-size: 17px; margin-top: 6px; }
  .rule {
    position: absolute; left: 34px; right: 36px; top: 178px;
    height: 1px; background: var(--rule);
  }
  .contact-list { position: absolute; list-style: none; top: 194px; color: var(--white); font-size: 16px; }
  .contact-list li { display: flex; align-items: center; gap: 10px; height: 26px; }
  .contact-left { left: 34px; }
  .contact-right { right: 36px; text-align: right; }
  .contact-right li { justify-content: flex-end; }
  .contact-right .stack { line-height: 22px; }
  .icon { width: 16px; height: 16px; flex: none; }
  .band {
    position: absolute; left: 0; right: 0; bottom: 0; height: 9px;
    background: linear-gradient(90deg, var(--red) 0 76%, var(--cyan) 76% 100%);
  }
</style>
</head>
<body>

<section class="card card-back" aria-label="Card back">
  <div class="back-brand">
    <span class="mark"></span>
    <span class="name">Veldmark Supplies</span>
  </div>
</section>

<section class="card card-front" aria-label="Card front">
  <div class="brand">
    <span class="mark"></span>
    <span class="name">Veldmark Supplies</span>
  </div>

  <div class="person">
    <div class="full-name">Jonathan Smith</div>
    <div class="role">Owner</div>
  </div>

  <div class="rule"></div>

  <ul class="contact-list contact-left">
    <li>
      <svg class="icon" viewBox="0 0 16 16" aria-hidden="true"><path fill="#12b4d6" d="M3.5 1.5l2.5 2.6-1.5 1.8c.8 1.9 2.2 3.3 4.1 4.1l1.8-1.5 2.6 2.5-1.6 2.4C6.8 13.2 2.8 9.2 1.6 3.1z"/></svg>
      044-123 456 789
    </li>
    <li>
      <svg class="icon" viewBox="0 0 16 16" aria-hidden="true"><rect x="4" y="1" width="8" height="14" rx="1.5" fill="none" stroke="#12b4d6" stroke-width="1.6"/><circle cx="8" cy="12.5" r=".9" fill="#12b4d6"/></svg>
      044-123 456 789
    </li>
    <li>
      <svg class="icon" viewBox="0 0 16 16" aria-hidden="true"><rect x="1" y="3" width="14" height="10" fill="#12b4d6"/><path d="M1 3l7 6 7-6" fill="none" stroke="#1c1c1d" stroke-width="1.3"/></svg>
      info@webname.com
    </li>
  </ul>

  <ul class="contact-list contact-right">
    <li>
      www.websitename.com
      <svg class="icon" viewBox="0 0 16 16" aria-hidden="true"><circle cx="8" cy="8" r="7" fill="#12b4d6"/><path d="M4 5c2 0 2 2 4 2s1 3 0 4M10 3c0 2 2 2 3 3" fill="none" stroke="#1c1c1d" stroke-width="1.2"/></svg>
    </li>
    <li>
      <span class="stack">421, Address line goes here<br>45452, Country name</span>
      <svg class="icon" viewBox="0 0 16 16" aria-hidden="true"><path fill="#12b4d6" d="M8 1a5 5 0 0 0-5 5c0 4 5 9 5 9s5-5 5-9a5 5 0 0 0-5-5zm0 7a2 2 0 1 1 0-4 2 2 0 0 1 0 4z"/></svg>
    </li>
  </ul>

  <div class="band"></div>
</section>

</body>
</html>
```